Medical VIP club - small design

Please read the specs in a design brief attached. Also we don't have logo in a Vector format and attaching the only version we have.

Club

```html
<!DOCTYPE html>
<html lang="en">
<head>
<meta charset="utf-8">
<title>Vitalia — VIP Club</title>
<link rel="stylesheet" href="https://fonts.googleapis.com/css2?family=Arimo:wght@400;700&display=swap">
<style>
  :root{
    --navy-deep:#1a2f6e;
    --navy:#25428f;
    --band:#a9c4f2;
    --tab-top:#3a8cff;
    --tab-bottom:#1257e0;
    --tab-active-top:#40b8ff;
    --tab-active-bottom:#1a8ef0;
    --tab-dark-top:#1a3fd8;
    --tab-dark-bottom:#0a1fb8;
    --title-top:#5d6b99;
    --title-bottom:#3b4775;
    --text:#3a3a3a;
    --rule:#e4e4e4;
    --white:#ffffff;
    --logo:#2a8cf0;
  }
  *{box-sizing:border-box;margin:0;padding:0}
  html,body{width:1200px;height:876px;overflow:hidden}
  body{background:var(--navy-deep);font-family:"Arimo",Arial,sans-serif}
  .page{position:relative;width:980px;height:715px;transform:scale(1.22449);transform-origin:0 0;
    background:var(--navy-deep)}

  .header{position:absolute;left:0;top:0;width:980px;height:228px;
    background:linear-gradient(180deg,#5a6e9e 0,#2a4688 6px,var(--navy) 60%,#2c4a98 195px,var(--band) 196px,#d4e2fa 212px,#8fb0ea 228px)}
  .brand{position:absolute;left:34px;top:58px;display:flex;align-items:center;gap:10px}
  .brand-dot{width:34px;height:34px;border-radius:50%;background:var(--logo)}
  .brand-name{font-size:46px;font-weight:700;color:var(--logo);letter-spacing:-1px}

  .phone{position:absolute;left:644px;top:42px;display:flex;align-items:center;gap:18px}
  .phone-badge{width:86px;height:86px;border-radius:50%;
    background:radial-gradient(circle at 45% 30%,#7fb6ff 0,#2a66d6 45%,#0f2f8a 100%);
    box-shadow:0 3px 6px rgba(0,0,0,.45);display:flex;align-items:center;justify-content:center}
  .phone-number{font-size:36px;font-weight:700;color:var(--white);
    text-shadow:0 0 2px #0a1a4a,0 2px 3px #0a1a4a}

  .nav{position:absolute;left:20px;top:170px;display:flex;gap:3px}
  .nav a{display:flex;align-items:center;justify-content:center;width:155px;height:58px;padding-top:8px;
    border-radius:12px 12px 0 0;color:var(--white);font-size:16px;text-decoration:none;
    background:linear-gradient(180deg,#6aaeff 0,var(--tab-top) 30%,var(--tab-bottom) 60%,#2a78f0 100%)}
  .nav a.is-active{background:linear-gradient(180deg,#7ad2ff 0,var(--tab-active-top) 30%,var(--tab-active-bottom) 60%,#36a8f5 100%)}
  .nav a.is-highlight{background:linear-gradient(180deg,#4060f0 0,var(--tab-dark-top) 30%,var(--tab-dark-bottom) 60%,#1020c0 100%)}

  .content{position:absolute;left:20px;top:236px;width:945px;height:396px;background:var(--white);
    border:1px solid #c9c9c9;overflow:hidden}
  .content-title{position:absolute;left:3px;top:3px;width:938px;height:44px;padding-left:13px;
    display:flex;align-items:center;color:var(--white);font-size:20px;font-weight:400;
    background:linear-gradient(180deg,var(--title-top),var(--title-bottom));
    box-shadow:0 2px 3px rgba(0,0,0,.3)}
  .club-item{position:absolute;left:13px;display:flex;gap:16px}
  .club-item--first{top:68px}
  .club-item--second{top:230px}
  .club-photo{flex:none;width:126px;height:115px;
    background:linear-gradient(180deg,#5a9ae8 0,#bfe0f5 45%,#eef0ee 60%,#c9b9a6 100%);
    border:1px solid #bbb;box-shadow:2px 3px 4px rgba(0,0,0,.35)}
  .club-text{width:775px;max-height:126px;overflow:hidden;font-size:12px;line-height:18px;color:var(--text);margin-top:-1px}
  .divider{position:absolute;left:16px;top:207px;width:920px;border-top:1px solid var(--rule)}

  .footer{position:absolute;left:0;top:640px;width:980px;height:75px;
    background:linear-gradient(180deg,#4a64a8 0,#2c4a98 8px,var(--navy) 60%,#1e3a84 100%);
    border-top:1px solid #6a84c0;border-bottom:2px solid #6a84c0}
  .social{position:absolute;left:20px;top:23px;display:flex;gap:4px}
  .social span{width:30px;height:30px;border-radius:3px}
  .social .s1{background:#3b5998}
  .social .s2{background:#4fc3ec}
  .social .s3{background:#f27a1a}
  .copyright{position:absolute;left:0;width:980px;top:37px;text-align:center;color:var(--white);font-size:11px}
  .footer-brand{position:absolute;right:18px;top:22px;display:flex;align-items:center;gap:6px}
  .footer-brand .brand-dot{width:20px;height:20px}
  .footer-brand .brand-name{font-size:28px;letter-spacing:0}
</style>
</head>
<body>
<div class="page">
  <header class="header">
    <div class="brand"><span class="brand-dot"></span><span class="brand-name">vitalia</span></div>
    <div class="phone">
      <div class="phone-badge">
        <svg width="46" height="40" viewBox="0 0 46 40" aria-hidden="true">
          <path d="M3 12 C3 4 43 4 43 12 L43 16 L33 16 L33 11 L13 11 L13 16 L3 16 Z" fill="#fff"/>
          <path d="M10 18 L36 18 L42 36 L4 36 Z" fill="#fff"/>
          <circle cx="23" cy="27" r="5" fill="#2a5fcc"/>
        </svg>
      </div>
      <span class="phone-number">416-555-555</span>
    </div>
    <nav class="nav">
      <a href="#">About Us</a>
      <a href="#">VIP Club</a>
      <a href="#" class="is-active">Services</a>
      <a href="#">Packages &amp; Prices</a>
      <a href="#" class="is-highlight">Registration</a>
      <a href="#">Contacts</a>
    </nav>
  </header>

  <main class="content">
    <h1 class="content-title">VIP Club</h1>
    <section class="club-item club-item--first">
      <div class="club-photo" role="img" aria-label="Couple in white robes on a resort terrace overlooking the sea"></div>
      <p class="club-text">Lorem ipsum dolor sit amet consecutor. Lorem ipsum dolor sit amet consecutor. Lorem ipsum dolor sit amet consecutor. Lorem ipsum dolor sit amet consecutor. Lorem ipsum dolor sit amet consecutor. Lorem ipsum dolor sit amet consecutor. Lorem ipsum dolor sit amet consecutor. Lorem ipsum dolor sit amet consecutor. Lorem ipsum dolor sit amet consecutor. Lorem ipsum dolor sit amet consecutor. Lorem ipsum dolor sit amet consecutor. Lorem ipsum dolor sit amet consecutor. Lorem ipsum dolor sit amet consecutor. Lorem ipsum dolor sit amet consecutor. Lorem ipsum dolor sit amet consecutor. Lorem ipsum dolor sit amet consecutor. Lorem ipsum dolor sit amet consecutor. Lorem ipsum dolor sit amet consecutor. Lorem ipsum dolor sit amet consecutor. Lorem ipsum dolor sit amet consecutor. Lorem ipsum dolor sit amet consecutor. Lorem ipsum dolor sit amet consecutor. Lorem ipsum dolor sit amet consecutor. Lorem ipsum dolor sit amet consecutor. Lorem ipsum dolor sit amet consecutor. Lorem ipsum dolor sit amet consecutor. Lorem ipsum dolor sit amet consecutor.</p>
    </section>
    <div class="divider"></div>
    <section class="club-item club-item--second">
      <div class="club-photo" role="img" aria-label="Couple in white robes on a resort terrace overlooking the sea"></div>
      <p class="club-text">Lorem ipsum dolor sit amet consecutor. Lorem ipsum dolor sit amet consecutor. Lorem ipsum dolor sit amet consecutor. Lorem ipsum dolor sit amet consecutor. Lorem ipsum dolor sit amet consecutor. Lorem ipsum dolor sit amet consecutor. Lorem ipsum dolor sit amet consecutor. Lorem ipsum dolor sit amet consecutor. Lorem ipsum dolor sit amet consecutor. Lorem ipsum dolor sit amet consecutor. Lorem ipsum dolor sit amet consecutor. Lorem ipsum dolor sit amet consecutor. Lorem ipsum dolor sit amet consecutor. Lorem ipsum dolor sit amet consecutor. Lorem ipsum dolor sit amet consecutor. Lorem ipsum dolor sit amet consecutor. Lorem ipsum dolor sit amet consecutor. Lorem ipsum dolor sit amet consecutor. Lorem ipsum dolor sit amet consecutor. Lorem ipsum dolor sit amet consecutor. Lorem ipsum dolor sit amet consecutor. Lorem ipsum dolor sit amet consecutor. Lorem ipsum dolor sit amet consecutor. Lorem ipsum dolor sit amet consecutor. Lorem ipsum dolor sit amet consecutor. Lorem ipsum dolor sit amet consecutor. Lorem ipsum dolor sit amet consecutor.</p>
    </section>
  </main>

  <footer class="footer">
    <div class="social" aria-label="Social links">
      <span class="s1"></span><span class="s2"></span><span class="s3"></span>
    </div>
    <p class="copyright">Copyright ©2010 Vitalia. All Rights Reserved</p>
    <div class="footer-brand"><span class="brand-dot"></span><span class="brand-name">vitalia</span></div>
  </footer>
</div>
</body>
</html>
```